Career Development Skills | Business Card & Logo Design

We are looking for a business card including logo design for a new Sydney based business called 'Bright Pathwork'.
We offer a range of services that focus on building the Employability or Employment skills for individuals focusing on job seekers and those interested in building skills required to develop their career. Employability skills are required not only to gain employment, but also to progress within an organisation so as to achieve one's potential.
Updates
Target Market(s)
Our client targets include corporates and govt agencies looking to build skills within their current employee base or assist staff in the transition between roles or workplaces.
Industry/Entity Type
Business
Look and feel
Each slider illustrates characteristics of the customer's brand and the style your logo design should communicate.

```html
<!DOCTYPE html>
<html lang="en">
<head>
<meta charset="utf-8">
<title>Bright Pathwork – Business Cards</title>
<link href="https://fonts.googleapis.com/css2?family=Crimson+Pro:wght@400;600;800&display=swap" rel="stylesheet">
<style>
  :root {
    --sky-deep: #2f86cc;
    --sky-light: #5aa6df;
    --mist: #d7dde3;
    --silver: #e9eced;
    --steel: #9aa3aa;
    --ink: #111111;
    --brand-red: #c8141a;
    --rule: #1a1a1a;
  }
  * { margin: 0; padding: 0; box-sizing: border-box; }
  html, body {
    width: 1200px; height: 1058px; overflow: hidden; background: #ffffff;
  }
  .sheet {
    position: relative; width: 1200px; height: 1058px;
    font-family: "Crimson Pro", Georgia, serif; color: var(--ink);
  }
  .card { position: absolute; top: 0; height: 1058px; overflow: hidden; }
  .card--front {
    left: 0; width: 595px;
    background: linear-gradient(180deg, var(--sky-deep) 0%, var(--sky-light) 35%, var(--mist) 70%, var(--silver) 100%);
  }
  .card--back {
    left: 598px; width: 602px;
    background: linear-gradient(90deg, var(--sky-deep) 0%, var(--mist) 30%, var(--silver) 60%, var(--sky-light) 85%, var(--sky-deep) 100%);
  }
  .rule { position: absolute; background: var(--rule); }
  .photo { position: absolute; }
  .photo--front-ladder {
    left: 90px; top: 0; width: 505px; height: 1058px;
    background: linear-gradient(180deg, #b9c0c6 0%, var(--silver) 45%, #f4f4f4 75%, var(--steel) 100%);
    clip-path: polygon(48% 0, 62% 0, 100% 80%, 100% 100%, 0 100%, 0 92%);
  }
  .photo--back-ladder {
    left: 0; top: 505px; width: 602px; height: 553px;
    background: linear-gradient(90deg, var(--steel) 0%, var(--silver) 40%, #f2f2f2 70%, #c4cacf 100%);
    clip-path: polygon(0 0, 100% 42%, 100% 50%, 0 100%);
  }
  .vertical { position: absolute; writing-mode: vertical-rl; white-space: nowrap; }
  .fax-line, .phone-line { position: absolute; font-size: 27px; font-weight: 600; line-height: 1; }
  .brand-name { color: var(--brand-red); font-weight: 800; }
  .brand-name--front { left: 410px; top: 40px; font-size: 92px; line-height: 1; }
  .brand-name--back { left: 510px; top: 30px; font-size: 62px; line-height: 1; }
  .person-name { left: 335px; top: 212px; font-size: 42px; font-weight: 600; }
  .contact { font-size: 32px; font-weight: 600; line-height: 1; }
  .address { left: 10px; top: 34px; font-size: 20px; font-weight: 600; line-height: 30px; }
  .web { left: 90px; top: 612px; font-size: 34px; line-height: 1; }
  .email { left: 30px; top: 532px; font-size: 34px; line-height: 1; }
</style>
</head>
<body>
<main class="sheet">
  <section class="card card--front" aria-label="Business card front">
    <div class="photo photo--front-ladder" role="img" aria-label="Photograph of a silver metal ladder rising in perspective"></div>
    <div class="rule" style="left:0; top:80px; width:595px; height:1px;"></div>
    <p class="phone-line" style="left:14px; top:110px;">Ph: (02) 9555 0142</p>
    <p class="fax-line" style="left:14px; top:156px;">Fx: (02) 9555 0143</p>
    <h1 class="vertical brand-name brand-name--front">Bright Pathwork</h1>
  </section>

  <section class="card card--back" aria-label="Business card back">
    <div class="photo photo--back-ladder" role="img" aria-label="Photograph of a silver metal ladder receding into the distance"></div>
    <div class="rule" style="left:0; top:105px; width:602px; height:1px;"></div>
    <div class="rule" style="left:540px; top:0; width:1px; height:1058px;"></div>
    <h2 class="vertical brand-name brand-name--back">Bright Pathwork</h2>
    <p class="vertical person-name">Daniel Hart</p>
    <p class="vertical contact" style="left:275px; top:200px;">Phone: (02) 9555 0142</p>
    <p class="vertical contact" style="left:225px; top:200px;">Fax:&nbsp;&nbsp; (02) 9555 0143</p>
    <address class="vertical address" style="font-style:normal;">
      <span>Level 12</span><br>
      <span>Harbourview Tower 3</span><br>
      <span>88 Keel Street</span><br>
      <span>Harbourview, Sydney 2000</span>
    </address>
    <p class="vertical web">brightpathwork.com.au</p>
    <p class="vertical email">daniel@brightpathwork.com.au</p>
  </section>
</main>
</body>
</html>
```